Corporate Business Card

Very professional, Modern, Not to busy, include phone address email, website
(253) 617-4930, 18761 52nd Avenue S, Kent, WA 98047, martin@plumlinegroup.com, varkoworks.com

Target Market(s)

Manufacturing

Industry/Entity Type

Aero, machining, manufacturing, Off road racing

Contact Information for Business Card

Phone, address email, website

```html
<!DOCTYPE html>
<html lang="en">
<head>
<meta charset="utf-8">
<title>Varko Works — Business Card</title>
<link rel="stylesheet" href="https://fonts.googleapis.com/css2?family=Roboto:wght@400;700&family=Russo+One&display=swap">
<style>
  :root {
    --stage: #2b2b2b;
    --navy: #2c3a6a;
    --navy-ink: #27346a;
    --red: #b8252b;
    --paper: #eeeeee;
    --paper-shade: #dcdcdc;
    --white: #f2f2f2;
  }
  * { box-sizing: border-box; margin: 0; padding: 0; }
  html, body {
    width: 1200px; height: 1138px; overflow: hidden;
    background: var(--stage);
    font-family: "Roboto", sans-serif;
  }
  .card {
    position: absolute;
    border-radius: 16px;
    overflow: hidden;
  }
  /* Front */
  .card--front {
    left: 274px; top: 186px; width: 623px; height: 376px;
    background: var(--navy);
  }
  .brand {
    position: absolute;
    color: var(--white);
    font-family: "Roboto", sans-serif;
    font-weight: 700;
    white-space: nowrap;
    letter-spacing: 1px;
  }
  .card--front .brand {
    left: 0; right: 0; top: 112px;
    text-align: center;
    font-size: 66px; line-height: 76px;
  }
  .rule {
    position: absolute; height: 2px; background: var(--white);
  }
  .card--front .rule { left: 106px; width: 411px; top: 212px; }
  .site {
    position: absolute; left: 0; right: 0; top: 326px;
    text-align: center;
    color: var(--white);
    font-size: 17px; letter-spacing: 9.6px;
    text-indent: 9.6px;
  }
  .site .accent { color: var(--red); }

  /* Back */
  .card--back {
    left: 276px; top: 608px; width: 618px; height: 374px;
    background: linear-gradient(180deg, var(--paper) 0%, var(--paper) 60%, var(--paper-shade) 100%);
  }
  .card--back .panel { position: absolute; inset: 0; }
  .card--back .brand {
    left: 32px; top: 150px;
    font-size: 36px; line-height: 44px;
  }
  .card--back .rule { left: 32px; width: 236px; top: 205px; }

  .person {
    position: absolute; left: 337px; top: 106px;
    color: var(--navy-ink);
    font-family: "Russo One", sans-serif;
    font-size: 23px; letter-spacing: 0.3px;
  }
  .contact {
    position: absolute; left: 337px; top: 146px;
    list-style: none;
    color: var(--navy-ink);
    font-size: 17px; line-height: 24.3px;
  }
  .contact li { position: relative; padding-left: 32px; }
  .contact svg { position: absolute; left: 0; top: 5px; width: 15px; height: 15px; fill: var(--red); }
  .contact .gap { margin-top: 0; }
</style>
</head>
<body>

<section class="card card--front">
  <div class="brand">VARKO WORKS</div>
  <div class="rule"></div>
  <div class="site">www.varko<span class="accent">works</span>.com</div>
</section>

<section class="card card--back">
  <svg class="panel" viewBox="0 0 618 374" width="618" height="374" aria-hidden="true">
    <path d="M252 0 Q378 187 268 374 L248 374 Q366 187 252 0 Z" fill="var(--red)"/>
    <path d="M0 0 H252 Q366 187 248 374 H0 Z" fill="var(--navy)"/>
  </svg>
  <div class="brand">VARKO WORKS</div>
  <div class="rule"></div>

  <h1 class="person">MARTIN KELLER</h1>
  <ul class="contact">
    <li>
      <svg viewBox="0 0 16 16"><path d="M1 6 Q8 1 15 6 L13 8 L11 6.5 L11 5 Q8 4 5 5 L5 6.5 L3 8 Z M4 8 H12 L13.5 14 H2.5 Z"/></svg>
      (253) 617-4930
    </li>
    <li>
      <svg viewBox="0 0 16 16"><path d="M1 3 H15 V13 H1 Z M2.5 4.5 L8 9 L13.5 4.5 Z" fill-rule="evenodd"/></svg>
      martin@plumlinegroup.com
    </li>
    <li>
      <svg viewBox="0 0 16 16"><path d="M8 0.5 A5.5 5.5 0 0 1 13.5 6 C13.5 10 8 15.5 8 15.5 C8 15.5 2.5 10 2.5 6 A5.5 5.5 0 0 1 8 0.5 Z M8 3.8 A2.2 2.2 0 1 0 8 8.2 A2.2 2.2 0 1 0 8 3.8 Z" fill-rule="evenodd"/></svg>
      18761 52nd Avenue S,<br>Kent, WA 98047
    </li>
    <li>
      <svg viewBox="0 0 16 16"><path d="M8 1 A7 7 0 1 1 8 15 A7 7 0 1 1 8 1 Z M8 2.4 C6.6 4 6 6 6 8 C6 10 6.6 12 8 13.6 C9.4 12 10 10 10 8 C10 6 9.4 4 8 2.4 Z M2.5 7.3 H13.5 V8.7 H2.5 Z" fill-rule="evenodd"/></svg>
      www.varkoworks.com
    </li>
  </ul>
</section>

</body>
</html>
```